Home Page Design (+50 More Pages To Winning Designer!)

We have a 50+ page website, but we're starting with the home page. The winning designer will get all 50+ pages to design as a 2nd project, so make sure you do your best!

Velorane is in the private jet industry and needs a re-designed website.

We have created the structure for the website and content inside of Frandle.io (THESE ARE ONLY ROUGH A.I. GENERATED WIREFRAMES AND DO NOT NEED TO BE FOLLOWED EXACTLY) - https://www.frandle.io/app/project/K482915_qWmRtZaLs-KDnHoUvvy82QJ5cfhaR61trkwqlDV3Hm

Take the content from the 'Home Page' under the 'Wireframe' tab on the Frandle.io link above, but feel free to re-design the page in a better way as these are only A.I. generated wireframes.

We want a DARK theme.... High quality, luxurious feel, greyscale colors. Attached is a brand guideline (BUT THIS IS NOT A 100% BRAND GUIDELINE, YOU CAN CHANGE COLORS AND FONTS AND MAKE CHANGES IF YOU HAVE BETTER IDEAS) and attached is our logo. We are also attaching some examples of other apps and websites to give you a guideline of what we're looking for for this design project.

The final design MUST communicate luxury using high-quality imagery of large cabin luxurious private jets.
Updates

ENTRIES THAT DO NOT FOLLOW THE PROJECT BRIEF WILL BE AUTOMATICALLY DISCARDED. FOLLOW THE INSTRUCTIONS!

Industry/Entity Type

Travel

Number of Pages Required

1 page

Font styles to use
Sans Serif

Colors

Designer to choose colors to be used in the design.

Requirements
Must have
• Follow wireframe and use content in wireframe (see Frandle.io link)

```html
<!DOCTYPE html>
<html lang="en">
<head>
<meta charset="utf-8">
<title>Velorane — Luxury Private Jet Travel</title>
<link href="https://fonts.googleapis.com/css2?family=Urbanist:wght@300;400;500;600;700&family=Inter:wght@400;500;600&display=swap" rel="stylesheet">
<style>
:root{
  --bg:#000;
  --bg-soft:#0b0b0b;
  --panel:#2b2b2b;
  --line:#5a5a5a;
  --white:#fff;
  --text:#e8e8e8;
  --muted:#a3a3a3;
  --dim:#777;
  --gold:#c99a5b;
}
*{box-sizing:border-box;margin:0;padding:0}
html,body{width:1200px;height:5208px;overflow:hidden;background:var(--bg);color:var(--text);font-family:"Inter",sans-serif}
.page{position:relative;width:1200px;height:5208px;overflow:hidden}
.abs{position:absolute}
h1,h2,h3{font-family:"Urbanist",sans-serif;font-weight:400;color:var(--white)}
.btn{display:inline-block;font-family:"Inter",sans-serif;font-size:12px;font-weight:600;padding:9px 16px;border-radius:3px;border:1px solid var(--white);line-height:1}
.btn-light{background:var(--white);color:#000}
.btn-dark{background:transparent;color:var(--white)}
.btn-row{display:flex;gap:10px}
.eyebrow{display:flex;align-items:center;gap:6px;font-size:12px;color:var(--text)}
.eyebrow .sq{width:10px;height:10px;background:var(--white)}
.eyebrow .rule{width:36px;height:1px;background:var(--line)}
.copy{font-size:11px;line-height:1.45;color:var(--muted)}
.photo{border-radius:0}

/* nav */
.nav{top:0;left:0;width:1200px;height:80px;z-index:5;display:flex;align-items:center;padding:0 111px}
.brand{display:flex;align-items:center;gap:8px;font-family:"Urbanist",sans-serif;font-size:30px;font-weight:400;color:var(--white)}
.brand .mark{width:14px;height:14px;background:var(--white)}
.nav-links{display:flex;gap:46px;margin-left:60px;font-size:11px;color:var(--white)}
.nav-actions{margin-left:auto;display:flex;gap:8px}
.nav-actions .btn{font-size:10.5px;padding:9px 10px}

/* hero */
.hero{top:0;left:0;width:1200px;height:650px;background:
 radial-gradient(ellipse 60% 30% at 50% 52%,rgba(214,140,70,.55),transparent 70%),
 linear-gradient(180deg,#0d0d0f 0%,#2a2622 30%,#6b4b2e 50%,#2b231b 62%,#0c0b0a 82%,#000 100%)}
.hero-jet{left:260px;top:300px;width:680px;height:280px;background:radial-gradient(ellipse 50% 40% at 50% 50%,#8a8a8a,#3a3a3a 55%,transparent 75%);opacity:.7}
.hero-text{top:126px;left:0;width:1200px;text-align:center}
.hero-text h1{font-size:44px;font-weight:300;letter-spacing:.3px}
.hero-text p{width:660px;margin:12px auto 0;font-size:11.5px;line-height:1.3;color:var(--text)}
.hero-text .btn-row{justify-content:center;margin-top:16px}

/* split sections */
.split-copy{width:420px}
.split-copy h2{font-size:33px;line-height:1.1;margin-top:8px}
.split-copy .copy{margin-top:16px;width:400px}
.feature-list{margin-top:16px;display:flex;flex-direction:column;gap:14px}
.feature-list li{list-style:none;display:flex;align-items:center;gap:14px;font-size:10.5px;color:var(--text)}
.icon-ring{width:28px;height:28px;border:1px solid var(--line);border-radius:50%;display:flex;align-items:center;justify-content:center}
.framed{border:1px solid var(--line)}

/* window */
.window{border-radius:50%/44%;overflow:hidden;box-shadow:0 0 60px rgba(255,255,255,.08),inset 0 0 0 14px #1a1a1a}
.option{width:370px;padding:12px 14px}
.option h3{font-family:"Inter",sans-serif;font-size:14px;font-weight:600;display:flex;align-items:center;gap:6px}
.option h3 .sq{width:9px;height:9px;background:currentColor}
.option p{font-size:10.5px;line-height:1.4;margin-top:5px;color:var(--muted)}
.option.active{background:var(--white);border-radius:3px}
.option.active h3{color:#000}
.option.active p{color:#333}

.mini-feats{display:flex;gap:40px;margin-top:26px}
.mini-feats div{width:190px}
.mini-feats h4{font-size:13px;font-weight:600;color:var(--white)}
.mini-feats p{font-size:10.5px;color:var(--muted);line-height:1.4;margin-top:6px}

/* services */
.services h2{font-size:33px}
.service{display:flex;gap:14px;width:300px}
.service .ring{width:84px;height:84px;border:1px solid var(--line);border-radius:50%;flex:none;display:flex;align-items:center;justify-content:center;background:#0c0c0c}
.service h4{font-size:13px;font-weight:600;color:var(--white);margin-top:16px}
.service p{font-size:10.5px;color:var(--muted);line-height:1.4;margin-top:4px}

/* band photo */
.band{top:2418px;left:0;width:1200px;height:481px;background:
 radial-gradient(ellipse 18% 40% at 88% 40%,#cfc6bb,transparent 70%),
 radial-gradient(ellipse 22% 45% at 58% 35%,#6a5a4c,transparent 70%),
 linear-gradient(90deg,#3b2a1d 0%,#5b3f27 25%,#3a3230 50%,#5a5450 75%,#2c2b2b 100%)}
.band-text{top:2642px;left:0;width:1200px;text-align:center}
.band-text h2{font-size:32px}
.band-text p{font-size:11px;color:var(--text);margin-top:6px}
.band-text .btn-row{justify-content:center;margin-top:14px}

/* testimonial */
.testimonial{top:2899px;left:0;width:1200px;height:299px;background:var(--panel);text-align:center}
.stars{display:flex;justify-content:center;gap:6px;margin-top:56px}
.quote{font-family:"Urbanist",sans-serif;font-size:33px;line-height:1.15;color:var(--white);width:920px;margin:18px auto 0}
.author{display:flex;justify-content:center;align-items:center;gap:14px;margin-top:22px}
.avatar{width:42px;height:42px;border-radius:50%;background:radial-gradient(circle,#777,#222);border:2px solid #ddd}
.author .who{text-align:left;font-size:12px;color:var(--white)}
.author .who small{display:block;font-size:10px;color:var(--text)}
.author .divider{width:1px;height:36px;background:var(--line)}
.wordmark{font-family:"Inter",sans-serif;font-weight:600;font-size:19px;color:var(--white);display:flex;align-items:center;gap:8px}
.wordmark .sq{width:16px;height:16px;background:var(--white)}

/* trusted */
.trusted{top:3240px;left:0;width:1200px;text-align:center}
.trusted h2{font-size:33px}
.logo-row{display:flex;gap:12px;justify-content:center;margin-top:28px}
.logo-box{width:152px;height:64px;border:1px solid var(--line);border-radius:6px;display:flex;align-items:center;justify-content:center;gap:8px;font-size:20px;font-weight:600;color:#cfcfcf;background:#0c0c0c}
.logo-box .sq{width:16px;height:16px;background:#cfcfcf}

/* newsletter */
.news-copy h2{font-size:33px}
.input-wrap{display:flex;align-items:center;width:376px;height:44px;border:1px solid #cfcfcf;margin-top:26px;padding:4px}
.input-wrap span{flex:1;font-size:10px;color:var(--muted);padding-left:10px}
.input-wrap .btn{padding:9px 18px}

/* faq */
.faq-head{top:3898px;left:0;width:1200px;text-align:center}
.faq-head h2{font-size:33px}
.faq-head p{font-size:10.5px;color:var(--muted);margin-top:10px}
.faq-item{left:145px;width:907px;height:40px;background:var(--panel);display:flex;align-items:center;padding:0 22px;font-size:14px;font-weight:600;color:var(--white)}
.faq-item .sq{width:9px;height:9px;background:currentColor;margin-right:6px}
.faq-item svg{margin-left:auto}
.faq-open{top:4002px;height:90px;background:var(--white);color:#000;align-items:flex-start;flex-direction:column;padding:18px 22px}
.faq-open .q{display:flex;align-items:center;width:100%}
.faq-open p{font-size:10px;font-weight:400;line-height:1.4;color:#222;margin-top:6px;width:720px}

.still{top:4366px;left:143px;width:895px;display:flex;align-items:flex-start}
.still h2{font-size:33px}
.still p{font-size:10px;color:var(--muted);margin-top:8px}
.still .btn{margin-left:auto;margin-top:10px}

/* final cta */
.cta-bg{top:4440px;left:0;width:1200px;height:489px;background:
 radial-gradient(ellipse 30% 18% at 45% 30%,#7a7a7a,transparent 70%),
 radial-gradient(ellipse 80% 40% at 50% 0%,#3a3a3a,transparent 80%),
 linear-gradient(180deg,#101010 0%,#3d3d3d 28%,#1a1a1a 60%,#050505 100%)}
.cta-text{top:4720px;left:0;width:1200px;text-align:center}
.cta-text h2{font-size:33px}
.cta-text p{width:590px;margin:10px auto 0;font-size:10.5px;line-height:1.4;color:var(--text)}
.cta-text .btn-row{justify-content:center;margin-top:16px}
.cta-text .btn{padding:9px 30px}

/* footer */
.footer{top:4929px;left:0;width:1200px;height:279px;background:#000;border-top:1px solid #151515}
.f-col{top:40px}
.f-col h4{font-family:"Urbanist",sans-serif;font-size:20px;font-weight:400;color:var(--white)}
.f-col ul{list-style:none;margin-top:14px;display:flex;flex-direction:column;gap:7px;font-size:9px;color:var(--muted)}
.f-brand p{font-size:9px;color:var(--muted);line-height:1.35;width:150px;margin-top:10px}
.f-sub p{font-size:9px;color:var(--muted);margin-top:8px}
.f-input{width:194px;height:30px;border:1px solid #cfcfcf;margin-top:8px;font-size:9px;color:var(--muted);padding:9px 8px}
.f-sub .btn{margin-top:10px;font-size:11px;padding:8px 14px}
.f-sub small{display:block;font-size:8.5px;color:var(--muted);width:200px;margin-top:10px;line-height:1.3}
.f-bottom{top:216px;left:111px;width:978px;display:flex;align-items:center;font-size:9px;color:var(--muted)}
.socials{margin-left:auto;display:flex;gap:8px}
.socials span{width:20px;height:20px;border-radius:50%;background:#d9d9d9}
</style>
</head>
<body>
<div class="page">

  <!-- HERO -->
  <section class="abs hero" role="img" aria-label="Airliner on a runway at sunset, seen head-on"></section>
  <div class="abs hero-jet" aria-hidden="true"></div>

  <header class="abs nav">
    <div class="brand"><span>Velorane</span><span class="mark"></span></div>
    <nav class="nav-links"><span>Aircraft</span><span>Programs</span><span>WhyVelorane</span><span>Lifestyle ⌄</span></nav>
    <div class="nav-actions"><span class="btn btn-dark">Featured from Blog</span><span class="btn btn-light">Article Title</span></div>
  </header>

  <div class="abs hero-text">
    <h1>Experience the Ultimate in Luxury Jet Travel</h1>
    <p>Velorane offers fractional jet ownership, jet card programs, private jetlease programs, all access programs, helicopter access programs, andby the seat charter flights. Discover the perfect flight program for your needs.</p>
    <div class="btn-row"><span class="btn btn-light">Explore</span><span class="btn btn-dark">Learn More</span></div>
  </div>

  <!-- FRACTIONAL -->
  <section class="abs split-copy" style="top:682px;left:111px">
    <div class="eyebrow"><span class="sq"></span>Discover<span class="rule"></span></div>
    <h2>Experience the Luxury of Fractional Jet Ownership</h2>
    <p class="copy">With Velorane's fractional jet ownership program, you can enjoy the benefits of private jet travel without the hassle and expense of owning a whole aircraft. Our program offers flexibility, Convenience, and access to a fleet of luxurious jets, allowing you to travel in style and comfort.</p>
    <ul class="feature-list">
      <li><span class="icon-ring"><svg width="12" height="12" viewBox="0 0 12 12"><path d="M2 6l3 3 5-6" stroke="#fff" fill="none" stroke-width="1.4"/></svg></span>Flexible Ownership Options</li>
      <li><span class="icon-ring"><svg width="12" height="12" viewBox="0 0 12 12"><rect x="1.5" y="2.5" width="9" height="8" stroke="#fff" fill="none"/><path d="M1.5 5h9" stroke="#fff"/></svg></span>Convenient Booking Process</li>
      <li><span class="icon-ring"><svg width="12" height="12" viewBox="0 0 12 12"><path d="M2 10L10 2M5 2h5v5" stroke="#fff" fill="none" stroke-width="1.4"/></svg></span>Luxurious Fleet of Jets</li>
    </ul>
    <div class="btn-row" style="margin-top:18px"><span class="btn btn-light">Learn More</span><span class="btn btn-dark">Sign Up</span></div>
  </section>
  <div class="abs framed" style="top:682px;left:660px;width:427px;height:425px"></div>
  <div class="abs photo" style="top:667px;left:646px;width:428px;height:425px;background:linear-gradient(180deg,#a8adb3 0%,#c7c9cb 45%,#8c847a 60%,#a09482 100%)" role="img" aria-label="Businessman in a suit leaning on a propeller aircraft on the apron"></div>

  <!-- WINDOW + OPTIONS -->
  <div class="abs window" style="top:1155px;left:121px;width:354px;height:420px;background:radial-gradient(ellipse at 50% 45%,#c9c3ba,#6f6a66 55%,#2a2a2a 80%)" role="img" aria-label="Smiling man holding a tablet, framed by an aircraft window"></div>
  <div class="abs option active" style="top:1244px;left:656px"><h3><span class="sq"></span>Flexible Ownership Options Available</h3><p>Choose from a variety of ownership programs and enjoy the freedom to fly on your own terms.</p></div>
  <div class="abs option" style="top:1343px;left:656px"><h3><span class="sq"></span>Convenient Jet Card Programs</h3><p>Access a fleet of private jets with our exclusive jet card programs, offering flexibility and convenience.</p></div>
  <div class="abs option" style="top:1431px;left:656px"><h3><span class="sq"></span>Flexible Lease Programs</h3><p>Experience the luxury of private jet travel without the commitment with our flexible lease programs.</p></div>

  <!-- LEASE -->
  <section class="abs split-copy" style="top:1638px;left:111px;width:440px">
    <div class="eyebrow"><span class="sq"></span>experience<span class="rule"></span></div>
    <h2>Experience the luxury of Private jet travel without the Commitment with our flexible lease Programs.</h2>
    <p class="copy">Discover the ultimate in luxury and convenience with Velorane. Our exclusive private aviation solutions provide you with unparalleled access to the world of private jets, ensuring a seamless and extraordinary travel experience.</p>
    <div class="mini-feats">
      <div><h4>Convenience</h4><p>Enjoy hassle-free travel with our flexible scheduling and personalized services.</p></div>
      <div><h4>Luxury</h4><p>Indulge in the lavish amenities and Exquisite interiors of our private jets.</p></div>
    </div>
    <div class="btn-row" style="margin-top:36px"><span class="btn btn-light">Learn More</span><span class="btn btn-dark">Sign Up</span></div>
  </section>
  <div class="abs framed" style="top:1652px;left:640px;width:447px;height:425px"></div>
  <div class="abs photo" style="top:1640px;left:622px;width:450px;height:425px;background:linear-gradient(160deg,#d4c9bd 0%,#9e8b78 40%,#5b4a3c 70%,#2a2320 100%)" role="img" aria-label="Woman in a trench coat with a leather bag walking toward a private jet"></div>

  <!-- SERVICES -->
  <section class="abs services" style="top:2137px;left:111px;width:978px">
    <div class="eyebrow"><span></span>Luxury<span class="rule"></span></div>
    <h2 style="margin-top:6px">Experience the Ultimate in Private Jet Travel</h2>
    <p class="copy" style="width:560px;margin-top:8px">Velorane offers a wide range of exclusive services to meet your private jet travel needs. From fractional jet ownership to on-demand charter flights, we provide the highest level of luxury and convenience.</p>
    <div class="abs btn-row" style="top:34px;right:0"><span class="btn btn-light">Learn More</span><span class="btn btn-dark">Sign Up</span></div>
    <div style="display:flex;justify-content:space-between;margin-top:28px">
      <div class="service"><span class="ring"><svg width="36" height="36" viewBox="0 0 36 36"><circle cx="18" cy="18" r="16" fill="#fff"/><path d="M13 12a8 8 0 1 0 10 0M18 9v9" stroke="#000" stroke-width="2" fill="none"/></svg></span><div><h4>On-Demand Charter</h4><p>Fly anywhere, anytime with our on-demand charter service.</p></div></div>
      <div class="service"><span class="ring"><svg width="36" height="36" viewBox="0 0 36 36"><circle cx="18" cy="18" r="16" fill="#fff"/><path d="M11 22a5 5 0 0 1 2-9 6 6 0 0 1 11 1 4 4 0 0 1 1 8z" fill="#000"/></svg></span><div><h4>Global Medical Response &amp; Recovery</h4><p>We provide specialized medical transportation services worldwide.</p></div></div>
      <div class="service"><span class="ring"><svg width="36" height="36" viewBox="0 0 36 36"><path d="M6 24h8l6 3 10-6M12 14h6v4" stroke="#fff" stroke-width="2" fill="none"/><circle cx="22" cy="12" r="4" fill="#fff"/></svg></span><div><h4>Fractional Jet Ownership</h4><p>Enjoy the benefits of owning a private jet without the hassles.</p></div></div>
    </div>
  </section>

  <!-- BAND -->
  <section class="abs band" role="img" aria-label="Woman on a phone call inside a wood-panelled private jet cabin"></section>
  <div class="abs band-text">
    <h2>Experience Luxury travel like never Before</h2>
    <p>Contact us today to book your exclusive jet experience</p>
    <div class="btn-row"><span class="btn btn-light">Learn More</span><span class="btn btn-dark">Sign Up</span></div>
  </div>

  <!-- TESTIMONIAL -->
  <section class="abs testimonial">
    <div class="stars">
      <svg width="70" height="24" viewBox="0 0 70 24"><path d="M0 12h70" stroke="var(--gold)" stroke-width="2"/><path d="M30 2l4 10-4 10" stroke="var(--gold)" stroke-width="2" fill="none"/></svg>
      <svg width="170" height="24" viewBox="0 0 170 24"><g fill="var(--white)"><path id="s" d="M12 1l3 8h8l-6.5 5 2.5 8-7-5-7 5 2.5-8L1 9h8z"/><use href="#s" x="30"/><use href="#s" x="60"/><use href="#s" x="90"/><use href="#s" x="120"/></g></svg>
    </div>
    <p class="quote">Velorane's services have exceeded my expectations. The convenience and luxury of flying with them is unmatched.</p>
    <div class="author">
      <span class="avatar" role="img" aria-label="Portrait of the reviewer"></span>
      <div class="who">Daniel Hart<small>CEO, Halcyon Group</small></div>
      <span class="divider"></span>
      <span class="wordmark"><span class="sq"></span>Corvane</span>
    </div>
  </section>

  <!-- TRUSTED -->
  <section class="abs trusted">
    <h2>Trusted by top-tier Companies Around the Globe</h2>
    <div class="logo-row">
      <span class="logo-box"><span class="sq"></span>Corvane</span>
      <span class="logo-box"><span class="sq"></span>Frandle</span>
      <span class="logo-box"><span class="sq"></span>Corvane</span>
      <span class="logo-box"><span class="sq"></span>Frandle</span>
      <span class="logo-box"><span class="sq"></span>Corvane</span>
      <span class="logo-box"><span class="sq"></span>Frandle</span>
    </div>
  </section>

  <!-- NEWSLETTER -->
  <section class="abs news-copy" style="top:3560px;left:111px;width:440px">
    <h2>Subscribe to our Newsletter</h2>
    <p class="copy" style="margin-top:6px">Stay updated with exclusive offers and industry news</p>
    <div class="input-wrap"><span>Your email address</span><span class="btn btn-light">Sign Up</span></div>
    <p class="copy" style="margin-top:10px">By joining, you agree to our Terms and Conditions</p>
  </section>
  <div class="abs window" style="top:3440px;left:683px;width:347px;height:390px;background:radial-gradient(ellipse at 50% 40%,#c8b49a,#6a5c4e 55%,#1c1c1c 82%)" role="img" aria-label="Smiling older man in a blazer reading a tablet, framed by an aircraft window"></div>

  <!-- FAQ -->
  <div class="abs faq-head"><h2>Frequently</h2><p>Find answers to common questions about Velorane's services and programs.</p></div>
  <div class="abs faq-item faq-open">
    <div class="q"><span class="sq"></span>What is Velorane?<svg width="14" height="14" viewBox="0 0 14 14"><path d="M2 9l5-5 5 5" stroke="#000" stroke-width="1.6" fill="none"/></svg></div>
    <p>Velorane is a company that offers fractional jet ownership, jet card programs, private jet leaseprograms, allaccess programs, helicopter access programs, and by the seat charter flights. We provide flexible and convenient options for individuals and businesses to access private aviation services.</p>
  </div>
  <div class="abs faq-item" style="top:4107px"><span class="sq"></span>How it works?<svg width="14" height="14" viewBox="0 0 14 14"><path d="M2 5l5 5 5-5" stroke="#fff" stroke-width="1.6" fill="none"/></svg></div>
  <div class="abs faq-item" style="top:4170px"><span class="sq"></span>Why choose Velorane?<svg width="14" height="14" viewBox="0 0 14 14"><path d="M2 5l5 5 5-5" stroke="#fff" stroke-width="1.6" fill="none"/></svg></div>
  <div class="abs faq-item" style="top:4230px"><span class="sq"></span>How to book?<svg width="14" height="14" viewBox="0 0 14 14"><path d="M2 5l5 5 5-5" stroke="#fff" stroke-width="1.6" fill="none"/></svg></div>
  <div class="abs faq-item" style="top:4291px"><span class="sq"></span>What are the benefits?<svg width="14" height="14" viewBox="0 0 14 14"><path d="M2 5l5 5 5-5" stroke="#fff" stroke-width="1.6" fill="none"/></svg></div>

  <div class="abs still"><div><h2>Still Have Questions?</h2><p>Contact us for more information.</p></div><span class="btn btn-light">Contact Us</span></div>

  <!-- FINAL CTA -->
  <section class="abs cta-bg" role="img" aria-label="Private jet flying over misty grey mountains"></section>
  <div class="abs cta-text">
    <h2>Experience Luxury Travel like Never Before</h2>
    <p>Discover the ultimate in private jet travel with Velorane. Whether you're looking for fractional jet ownership, jet card programs, Private jet lease Programs, all access programs, helicopter access programs, or by the seat Charter flights, we have the perfect solution for your travel needs.</p>
    <div class="btn-row"><span class="btn btn-light">Book</span><span class="btn btn-dark">Contact</span></div>
  </div>

  <!-- FOOTER -->
  <footer class="abs footer">
    <div class="abs f-col f-brand" style="left:111px"><div class="brand" style="font-size:28px"><span>Velorane</span><span class="mark"></span></div><p>Velorane offers private jet seat booking and the most affordable private jet charter solution. Velorane technology provides confirmed seats on private jets in seconds.</p></div>
    <div class="abs f-col" style="left:360px"><h4>About Us</h4><ul><li>Charter</li><li>Fleet</li><li>Destinations</li><li>Pricing</li><li>Contact</li></ul></div>
    <div class="abs f-col" style="left:545px"><h4>Services</h4><ul><li>Private Jets</li><li>Helicopters</li><li>Jet Cards</li><li>Membership</li><li>FAQ</li></ul></div>
    <div class="abs f-col" style="left:745px"><h4>Terms</h4><ul><li>Privacy</li><li>Careers</li><li>Press</li><li>Blog</li><li>Support</li></ul></div>
    <div class="abs f-col f-sub" style="left:891px"><h4>Subscribe</h4><p>Join our mailing list for the latest</p><div class="f-input">Enter email Address</div><span class="btn btn-light">Subscribe</span><small>By subscribing you agree to our Privacy Policy and consent to receive updates.</small></div>
    <div class="abs f-bottom"><span>© 2024 Velorane. All rights reserved Privacy PolicyTerms of Service Cookie Settings</span><div class="socials"><span></span><span></span><span></span><span></span><span></span></div></div>
  </footer>

</div>
</body>
</html>
```